Jolly Hounds Dog Behaviour, Training and Natural Healthcare Business Card Design

I am an experienced and qualified dog behavioural trainer and natural animal healthcare consultant offering a range of services to help pet dog owners with the "whole dog".
COLOURS: A soft light blue in the background - can be fading out or split, red should also feature
LOGO: Dog, healing hands, silhouette, shadow
SERVICES: Behaviour Consults, Training, Complex Skills Coaching Walking Coaching, Diet & Nutrition, Environmental Enrichment, Lifestyle and Lifestage Adaptations, Massage, Natural Health Options
BY LINE: Happy Dogs, Happy Owners
VALUES: Promoting communication and connection between dogs and their owners.
FOCUS: Nutritional guidance and environmental adaptation are often needed to complete the package and increase the success rate of training and behaviour modification.

Target Market(s)

Everyone who has a dog who they wish to improve their relationship with

Industry/Entity Type

Communication

Contact Information for Business Card

Jolly Hounds, Rebecca Thornbury, 0427 861350, jollyhounds7@fernpost.example, www.jollyhounds7.example, Qualified Dog Behavioural Trainer and Natural Animal Healthcare Consultant

Font styles to use
Sans Serif
Script

Colors
85cae6
ec2027

Requirements
Must have
• A clear indication that it is a dog services business. A raised feature
Should not have
• Pawprints, cartoons

```html
<!DOCTYPE html>
<html lang="en">
<head>
<meta charset="utf-8">
<title>Jolly Hounds Business Card</title>
<link rel="stylesheet" href="https://fonts.googleapis.com/css2?family=Arimo:wght@400;700&display=swap">
<style>
  :root {
    --page: #ece8e3;
    --blue-light: #2f86cc;
    --blue-deep: #0d56a8;
    --red-bright: #ec2027;
    --red-deep: #7e0f14;
    --cream: #f3ecd2;
    --white: #ffffff;
    --ink: #1c1c1c;
  }
  * { box-sizing: border-box; margin: 0; padding: 0; }
  html, body { width: 1200px; height: 1000px; overflow: hidden; }
  body {
    background: var(--page);
    font-family: "Arimo", Arial, sans-serif;
    display: flex;
    flex-direction: column;
    align-items: center;
    justify-content: center;
    gap: 40px;
  }
  .card {
    position: relative;
    width: 760px;
    height: 434px;
    border-radius: 26px;
    overflow: hidden;
    box-shadow: 0 10px 24px rgba(0,0,0,0.25);
    color: var(--white);
  }
  .card-bg { position: absolute; inset: 0; }
  .card-front .brand-mark {
    position: absolute; left: 310px; top: 30px;
  }
  .card-front .brand-name {
    position: absolute; top: 186px; width: 100%; text-align: center;
    font-size: 50px; font-weight: 700; letter-spacing: 2px; text-transform: uppercase;
  }
  .card-front .tagline {
    position: absolute; top: 246px; width: 100%; text-align: center;
    font-size: 24px; letter-spacing: 1px; text-transform: uppercase;
  }
  .card-front .website {
    position: absolute; top: 372px; width: 100%; text-align: center;
    font-size: 17px;
  }
  .card-back .brand-mark { position: absolute; left: 56px; top: 50px; }
  .card-back .brand-mark-name {
    position: absolute; left: 81px; top: 125px; width: 120px; text-align: center;
    font-size: 15px; font-weight: 700; line-height: 1.2;
    color: var(--blue-deep); text-transform: uppercase;
  }
  .card-back .divider {
    position: absolute; width: 1px; background: var(--white); opacity: 0.85;
  }
  .services-divider { left: 262px; top: 48px; height: 170px; }
  .contact-divider { left: 450px; top: 318px; height: 70px; }
  .services {
    position: absolute; left: 284px; top: 46px; width: 455px;
    font-size: 16.5px; line-height: 1.32;
  }
  .services-title { font-size: 20px; text-transform: uppercase; }
  .values {
    position: absolute; left: 0; top: 244px; width: 100%; height: 30px;
    line-height: 30px; text-align: center;
    font-size: 18px; color: var(--ink);
  }
  .person {
    position: absolute; left: 20px; top: 300px; width: 420px; text-align: center;
  }
  .person-name { font-size: 30px; font-weight: 400; }
  .person-title { font-size: 18px; line-height: 1.3; margin-top: 6px; }
  .contacts {
    position: absolute; left: 466px; top: 318px;
    list-style: none; font-size: 16px;
  }
  .contacts li { display: flex; align-items: center; gap: 8px; height: 34px; white-space: nowrap; }
  .contacts svg { flex: none; }
</style>
</head>
<body>

<section class="card card-front" aria-label="Card front">
  <svg class="card-bg" width="760" height="434" viewBox="0 0 760 434" aria-hidden="true">
    <defs>
      <linearGradient id="frontBlue" x1="0" y1="0" x2="0" y2="1">
        <stop offset="0" stop-color="#3a92d6"/>
        <stop offset="1" stop-color="#0f5bb0"/>
      </linearGradient>
      <radialGradient id="frontRed" cx="0.5" cy="0.3" r="0.8">
        <stop offset="0" stop-color="#ec2027"/>
        <stop offset="1" stop-color="#7e0f14"/>
      </radialGradient>
    </defs>
    <rect width="760" height="434" fill="url(#frontBlue)"/>
    <path d="M0 322 C 240 346, 540 326, 760 278 L760 434 L0 434 Z" fill="var(--cream)"/>
    <path d="M0 330 C 240 354, 540 334, 760 286 L760 434 L0 434 Z" fill="url(#frontRed)"/>
  </svg>
  <svg class="brand-mark" width="140" height="140" viewBox="0 0 140 140" aria-hidden="true">
    <circle cx="70" cy="70" r="64" fill="var(--cream)" stroke="var(--red-bright)" stroke-width="9"/>
  </svg>
  <h1 class="brand-name">Jolly Hounds</h1>
  <p class="tagline">Happy Dogs, Happy Owners</p>
  <p class="website">www.jollyhounds7.example</p>
</section>

<section class="card card-back" aria-label="Card back">
  <svg class="card-bg" width="760" height="434" viewBox="0 0 760 434" aria-hidden="true">
    <defs>
      <linearGradient id="backBlue" x1="0" y1="0" x2="1" y2="1">
        <stop offset="0" stop-color="#0f5bb0"/>
        <stop offset="1" stop-color="#2f86cc"/>
      </linearGradient>
      <radialGradient id="backRed" cx="0.55" cy="0.35" r="0.7">
        <stop offset="0" stop-color="#ec2027"/>
        <stop offset="1" stop-color="#7e0f14"/>
      </radialGradient>
    </defs>
    <rect width="760" height="434" fill="url(#backBlue)"/>
    <rect y="244" width="760" height="30" fill="var(--cream)"/>
    <rect y="274" width="760" height="160" fill="url(#backRed)"/>
  </svg>
  <svg class="brand-mark" width="170" height="170" viewBox="0 0 170 170" aria-hidden="true">
    <circle cx="85" cy="85" r="78" fill="var(--cream)" stroke="var(--red-bright)" stroke-width="10"/>
  </svg>
  <p class="brand-mark-name">Jolly<br>Hounds</p>

  <div class="divider services-divider"></div>
  <div class="services">
    <p class="services-title">Services</p>
    <p>Behaviour Consults, Training, Complex Skills Coaching Walking Coaching, Diet &amp; Nutrition, Environmental Enrichment, Lifestyle and Lifestage Adaptations, Massage, Natural Health Options</p>
  </div>

  <p class="values">Promoting communication and connection between dogs and their owners</p>

  <div class="person">
    <h2 class="person-name">Rebecca Thornbury</h2>
    <p class="person-title">Qualified Dog Behavioural Trainer<br>and Natural Animal Healthcare Consultant</p>
  </div>

  <div class="divider contact-divider"></div>
  <ul class="contacts">
    <li>
      <svg width="22" height="22" viewBox="0 0 22 22" aria-hidden="true">
        <circle cx="11" cy="11" r="10" fill="var(--white)"/>
        <rect x="7.5" y="4.5" width="7" height="13" rx="1.5" fill="var(--red-bright)"/>
        <rect x="9" y="6.5" width="4" height="7" fill="var(--white)"/>
      </svg>
      <span>0427 861350</span>
    </li>
    <li>
      <svg width="22" height="22" viewBox="0 0 22 22" aria-hidden="true">
        <circle cx="11" cy="11" r="10" fill="var(--white)"/>
        <rect x="5" y="7" width="12" height="8" fill="var(--red-bright)"/>
        <path d="M5 7 L11 12 L17 7" fill="none" stroke="var(--white)" stroke-width="1.2"/>
      </svg>
      <span>jollyhounds7@fernpost.example</span>
    </li>
  </ul>
</section>

</body>
</html>
```